Local massage therapist needs some new marketing material

Hi there! I am a massage therapist here in Denver, CO in Alder Bend(shopping and art district) of the city. My business is called Lumo Bodywork of Denver. My practice has an eastern influence and I do reflexology, thai massage and use Chinese herbs, etc. I know all my clients and pay close attention to details. I am also very respectful of tradition and it shows in how I work. I tend to like modern, clean, fun, Asian designs. I am wanting a new business card and brochure. I have a logo and branding for my business that I want used in the design. Currently, the sign for my building is purple and I think my logo was designed to be purple. I will attach pictures of it and can send whatever files are necessary so it can be integrated into the brochure, etc. I like the purple but open to using other colors as well. Thanks!
My website is lumobodyworkofdenver.example where info can be gathered about me and services/fees for brochure.
Updates

Just increased budget. Please see new feedback in discussion thread.

Thanks!

                                       HEY ALL,

Just wanted to let you know that I made a change to my website. It is on the Prices Page. I no longer have the frequent  flyer prices but I added discounts. Let me know if you have any questions. Thanks so much!

Target Market(s)

healthy, urban, educated, upper middle class, yogis

Industry/Entity Type

Marketing

Requirements
Must have
• logo stays purple
Should not have
• not too busy

```html
<!DOCTYPE html>
<html lang="en">
<head>
<meta charset="utf-8">
<title>Lumo Bodywork of Denver – Brochure</title>
<link rel="stylesheet" href="https://fonts.googleapis.com/css2?family=Marcellus&family=Open+Sans:wght@400;700&display=swap">
<style>
  :root {
    --purple: #6a2c91;
    --purple-band: #5b2a86;
    --ink: #4a4a4a;
    --paper: #ffffff;
    --rule: #d9d9d9;
    --bg: #f2f0ee;
  }
  * { box-sizing: border-box; margin: 0; padding: 0; }
  html, body { width: 1200px; height: 942px; overflow: hidden; background: var(--bg); }
  .brochure {
    position: relative; width: 1200px; height: 942px; background: var(--paper);
    display: grid; grid-template-columns: 400px 400px 400px;
    border-top: 12px solid var(--purple-band); border-bottom: 12px solid var(--purple-band);
  }
  .panel { position: relative; height: 918px; overflow: hidden; }
  .panel + .panel { border-left: 1px solid var(--rule); }
  .photo { position: absolute; left: 0; width: 100%; }
  .heading { font-family: "Marcellus", serif; color: var(--purple); font-weight: 400; }

  /* Panel 1 */
  .therapist-photo { top: 0; height: 303px; background: linear-gradient(135deg, #a9dde0 0%, #f6d4de 45%, #e9c89f 70%, #2d6f8c 100%); }
  .therapist-name { position: absolute; top: 60px; left: 30px; font-family: "Marcellus", serif; color: var(--purple); font-size: 21px; line-height: 1.3; }
  .intro-title { position: absolute; top: 320px; left: 25px; font-size: 39px; line-height: 1.35; }
  .about-title { position: absolute; top: 445px; left: 25px; font-size: 25px; }
  .about-copy { position: absolute; top: 482px; left: 25px; width: 355px; font-family: "Open Sans", sans-serif; font-size: 12.4px; line-height: 1.45; color: var(--ink); text-align: justify; }
  .about-copy p + p { margin-top: 7px; }
  .about-copy strong { font-size: 14px; }

  /* Panel 2 */
  .location-title { position: absolute; top: 76px; left: 22px; font-size: 34px; }
  .contact { position: absolute; top: 140px; left: 22px; font-family: "Open Sans", sans-serif; font-size: 15.5px; line-height: 1.75; color: var(--ink); }
  .contact .label { color: var(--purple); }
  .hours { position: absolute; top: 238px; left: 22px; font-family: "Open Sans", sans-serif; font-size: 15.5px; line-height: 1.75; color: var(--ink); }
  .studio-photo { top: 303px; height: 303px; background: linear-gradient(180deg, #cfe0ec 0%, #8c8a8e 35%, #b7b3b3 60%, #4f7a3a 100%); }
  .small-brand { position: absolute; top: 700px; left: 30px; display: flex; align-items: center; gap: 12px; }
  .small-brand .mark { width: 24px; height: 24px; border-radius: 50%; background: var(--purple); }
  .small-brand .name { font-family: "Marcellus", serif; color: var(--purple); font-size: 48px; letter-spacing: 8px; }
  .stones-photo { left: 255px; top: 650px; width: 130px; height: 250px; border-radius: 60px 60px 50px 50px; background: radial-gradient(ellipse at 50% 40%, #9a9a9a 0%, #5a5a5a 60%, #e8e8e8 100%); }

  /* Panel 3 */
  .main-brand { position: absolute; top: 230px; left: 0; width: 100%; display: flex; flex-direction: column; align-items: center; gap: 26px; }
  .main-brand .mark { width: 60px; height: 60px; border-radius: 50%; background: var(--purple); }
  .main-brand .name { font-family: "Marcellus", serif; color: var(--purple); font-size: 64px; letter-spacing: 14px; padding-left: 14px; }
  .tagline { position: absolute; top: 460px; left: 0; width: 100%; text-align: center; font-size: 38px; line-height: 1.4; }
  .spa-photo { top: 606px; height: 312px; background: linear-gradient(120deg, #efe6dc 0%, #d9a98a 40%, #8a5a3c 75%, #4a2e20 100%); }
</style>
</head>
<body>
<main class="brochure">
  <section class="panel panel-therapist">
    <div class="photo therapist-photo" role="img" aria-label="Portrait photo of the therapist against a soft pastel chevron backdrop"></div>
    <p class="therapist-name">Dana<br>Whitlow</p>
    <h2 class="heading intro-title">Get To Know Your<br>Therapist</h2>
    <h3 class="heading about-title">About</h3>
    <div class="about-copy">
      <p><strong>Dana Whitlow</strong> is a registered massage therapist, a member of the National Circle for Holistic Aromatherapy, Thai Bodywork Guild, American Touch Therapy Society, Bodywork Research Fund and Alliance for Massage Practitioners. She graduated from the Front Range Massage Institute and has formally studied Thai Massage techniques at the Lanna Traditional Massage School, Thailand. Presently, she is studying at Whole Path Healing Academy with students from around the world to better understand natural health, energy work and spiritual counseling.</p>
      <p>Dana began meditation as a teen and learned the benefits of quieting the mind. Feeling the call within herself to help others, Dana naturally gravitated toward massage therapy and natural healing. Dana enjoys helping to facilitate people on their journeys toward health and personal happiness. She believes in an energy (Chi) within us that when unobstructed, promotes our health and well-being. She trusts in the body's natural capacity to heal, and takes advantage of this power in her delivery of bodywork.</p>
    </div>
  </section>

  <section class="panel panel-location">
    <h2 class="heading location-title">Where We’re Located</h2>
    <div class="contact">
      <p>1480 E Alder Ave, Denver, CO 80206</p>
      <p><span class="label">P:</span> 303.555.0187</p>
      <p><span class="label">E:</span> info@lumobodyworkofdenver.example</p>
    </div>
    <div class="hours">
      <p>Tues - Fri 10am - 8pm Sat 10am-5pm</p>
      <p>(Appointments required) No walk-ins please.</p>
    </div>
    <div class="photo studio-photo" role="img" aria-label="Photo of the painted brick studio building surrounded by trees and shrubs"></div>
    <div class="small-brand">
      <span class="mark"></span>
      <span class="name">LUMO</span>
    </div>
    <div class="photo stones-photo" role="img" aria-label="Photo of stacked grey massage stones topped with a green leaf"></div>
  </section>

  <section class="panel panel-cover">
    <div class="main-brand">
      <span class="mark"></span>
      <span class="name">LUMO</span>
    </div>
    <h1 class="heading tagline">Your Path To Wellness<br>Begins Here!</h1>
    <div class="photo spa-photo" role="img" aria-label="Photo of a client receiving a back massage beside a bowl of herbs and spa items"></div>
  </section>
</main>
</body>
</html>
```